Vellmore Family Law, legal technician needs a website and design

I need a website for a family law practice. I specialize in collaborative law, unbundled services, and mediation. The website must contain my company logo (file attached), and the website must be a mixture of my personality and my profession. I have attached additional information to explain my personality and profession.

Target Market(s)

Lower through middle-class (income level up to $200,000 per year)

Coding

Coded - Design and coding required

Number of Pages Required

1 page

Requirements
Must have
• Must have enough pages to cover required content. I submitted below some content about the collaborative law process. All of the content is not necessary. However, the website must have enough content to clearly describe the services I offer. Use your professionalism and judgment regarding font, font size, etc.

```html
<!DOCTYPE html>
<html lang="en">
<head>
<meta charset="utf-8">
<title>Vellmore Family Law</title>
<link rel="stylesheet" href="https://fonts.googleapis.com/css2?family=Lato:wght@400;700;900&display=swap">
<style>
:root{
  --gold:#8b7b34;
  --gold-dark:#6f6128;
  --navy:#0f1731;
  --ink:#1d1d1f;
  --text:#3b3b3b;
  --muted:#f1f1f1;
  --blog-bg:#ebebeb;
  --footer:#1b1b1b;
  --footer-bar:#111111;
  --white:#ffffff;
}
*{box-sizing:border-box;margin:0;padding:0}
html,body{width:1200px;height:4769px;overflow:hidden}
body{position:relative;background:var(--white);font-family:'Lato',sans-serif;color:var(--text)}
.abs{position:absolute}
.btn{position:absolute;display:flex;align-items:center;justify-content:center;border-radius:30px;background:var(--navy);color:var(--white);font-weight:700;font-size:15px;letter-spacing:.3px;text-transform:uppercase;white-space:nowrap}
.btn.gold{background:var(--gold)}
.photo{position:absolute;overflow:hidden}

/* header */
.site-header{position:absolute;left:0;top:0;width:1200px;height:139px;background:var(--white)}
.brand{position:absolute;display:flex;align-items:center;gap:16px}
.brand-mark{width:60px;height:60px;background:var(--gold)}
.brand-name{font-weight:700;color:var(--gold);font-size:24px;line-height:1.1;text-transform:uppercase;letter-spacing:1px}
.phone-pill{left:911px;top:24px;width:215px;height:45px;font-size:18px;gap:10px;text-transform:none}
.main-nav{position:absolute;top:98px;left:0;width:1200px;font-size:14px;font-weight:700;color:var(--ink)}
.main-nav span{position:absolute;white-space:nowrap}
.main-nav .active{color:var(--gold)}

/* hero */
.hero{left:0;top:139px;width:1200px;height:643px;border-bottom-left-radius:110px;background:linear-gradient(120deg,#5c4a3c 0%,#8d7a6a 30%,#4c5560 60%,#2c3038 100%)}
.hero::after{content:"";position:absolute;inset:0;background:rgba(20,20,25,.35)}
.hero-title{position:absolute;left:0;width:1200px;text-align:center;color:var(--white);font-weight:900;text-transform:uppercase;text-shadow:0 2px 6px rgba(0,0,0,.35)}
.hero-title.big{font-size:70px;letter-spacing:.5px}
.hero-title.sub{font-size:31px;font-weight:700}
.dots{position:absolute;left:74px;display:flex;gap:9px}
.dots i{width:16px;height:16px;border-radius:50%;background:rgba(255,255,255,.45)}
.dots i:first-child{background:var(--white)}

/* section headings */
.section-title{position:absolute;font-weight:900;font-size:36px;color:var(--ink);text-transform:uppercase;white-space:nowrap}
.section-title.center{left:0;width:1200px;text-align:center}
.rule{position:absolute;height:5px;background:var(--gold)}

/* cards */
.card{position:absolute;width:326px;background:var(--white);border-radius:12px;box-shadow:0 2px 10px rgba(0,0,0,.18)}
.card-photo{position:absolute;left:0;top:0;width:326px;height:245px;border-radius:12px 12px 0 0}
.card-title{position:absolute;left:0;width:326px;text-align:center;color:var(--gold);font-weight:700;font-size:20px;text-transform:uppercase;line-height:28px}
.card-text{position:absolute;left:0;width:326px;text-align:center;font-size:14.5px;line-height:28px;color:var(--text)}
.card .btn{left:93px;width:140px;height:41px;font-size:14px;z-index:1}

/* how i do it */
.how{left:0;top:1539px;width:1200px;height:487px;background:var(--gold);border-top-right-radius:110px}
.video{left:74px;top:67px;width:513px;height:353px;border-radius:22px;background:radial-gradient(circle at 50% 45%,#5b5f63 0%,#2d3034 60%,#1b1d20 100%)}
.body-text{position:absolute;font-size:14.5px;line-height:30px}

/* contact form */
.field{position:absolute;height:50px;border-radius:25px;border:1px solid #e3e3e3;box-shadow:0 2px 8px rgba(0,0,0,.12);background:var(--white);font-size:14px;color:#333;padding:0 20px;display:flex;align-items:center;justify-content:space-between}
.field.area{height:186px;border-radius:28px;align-items:flex-start;padding-top:26px}

/* cta */
.cta{left:0;top:3982px;width:1200px;height:426px;border-top-right-radius:110px;background:linear-gradient(180deg,#6b5a25 0%,#4d4220 55%,#2e2a1a 100%)}

/* footer */
.site-footer{left:0;top:4408px;width:1200px;height:361px;background:var(--footer);color:var(--white)}
.foot-col{position:absolute;font-size:14px}
.foot-col h4{font-size:21px;font-weight:700;text-transform:uppercase;margin-bottom:14px}
.foot-col p{line-height:35px}
.foot-bar{position:absolute;left:0;top:302px;width:1200px;height:59px;background:var(--footer-bar);font-size:13px;color:#bdbdbd}
.social{position:absolute;top:21px;display:flex;gap:20px}
.social i{width:20px;height:20px;border-radius:50%;background:var(--white)}
</style>
</head>
<body>

<header class="site-header">
  <div class="brand" style="left:74px;top:44px">
    <div class="brand-mark"></div>
    <div class="brand-name">Vellmore<br>Family Law</div>
  </div>
  <div class="btn phone-pill">
    <svg width="16" height="16" viewBox="0 0 24 24" fill="#fff"><path d="M6.6 10.8a15.1 15.1 0 0 0 6.6 6.6l2.2-2.2a1 1 0 0 1 1-.25 11.4 11.4 0 0 0 3.6.57 1 1 0 0 1 1 1V20a1 1 0 0 1-1 1A17 17 0 0 1 3 4a1 1 0 0 1 1-1h3.5a1 1 0 0 1 1 1c0 1.25.2 2.450.57 3.6a1 1 0 0 1-.25 1z"/></svg>
    1-800-555-0148
  </div>
  <nav class="main-nav">
    <span class="active" style="left:552px">HOME</span>
    <span style="left:652px">ABOUT</span>
    <span style="left:759px">PRACTICE AREAS</span>
    <span style="left:939px">BLOG</span>
    <span style="left:1033px">CONTACT US</span>
  </nav>
</header>

<section class="photo hero" role="img" aria-label="Family meeting with a lawyer at a desk">
  <div style="position:relative;z-index:1;width:100%;height:100%">
    <h1 class="hero-title big" style="top:160px">Vellmore Family Law</h1>
    <p class="hero-title sub" style="top:248px">Collaborative Law and Unbundled Legal Service</p>
    <p class="hero-title sub" style="top:298px">in King County, Washington State</p>
    <div class="btn gold" style="left:474px;top:368px;width:252px;height:50px;font-size:16px">Contact Us Today</div>
    <div class="dots" style="top:564px"><i></i><i></i><i></i><i></i></div>
  </div>
</section>

<h2 class="section-title center" style="top:842px">What I Do</h2>
<div class="rule" style="left:509px;top:907px;width:182px"></div>

<article class="card" style="left:74px;top:965px;height:480px">
  <div class="card-photo" role="img" aria-label="Team working together around a table" style="background:linear-gradient(135deg,#4b4038,#9a8775 55%,#3a3d45)"></div>
  <h3 class="card-title" style="top:273px">Collaborative Law</h3>
  <p class="card-text" style="top:306px">Sed ut perspiciatis unde omnis iste natus<br>error sit voluptatem accusantium<br>doloremque laudantium, totam rem<br>aperiam, eaque ipsa quae.</p>
  <div class="btn" style="top:457px">Read More</div>
</article>
<article class="card" style="left:435px;top:965px;height:480px">
  <div class="card-photo" role="img" aria-label="Colleagues smiling at a laptop in an office" style="background:linear-gradient(135deg,#8a7056,#c9b79c 50%,#5a5048)"></div>
  <h3 class="card-title" style="top:273px">Unbundled Services</h3>
  <p class="card-text" style="top:306px">Sed ut perspiciatis unde omnis iste natus<br>error sit voluptatem accusantium<br>doloremque laudantium, totam rem<br>aperiam, eaque ipsa quae.</p>
  <div class="btn" style="top:457px">Read More</div>
</article>
<article class="card" style="left:800px;top:965px;height:480px">
  <div class="card-photo" role="img" aria-label="Mediation meeting in a bright room" style="background:linear-gradient(135deg,#d8dde2,#9aa3ad 50%,#3a4250)"></div>
  <h3 class="card-title" style="top:273px">Mediation</h3>
  <p class="card-text" style="top:306px">Sed ut perspiciatis unde omnis iste natus<br>error sit voluptatem accusantium<br>doloremque laudantium, totam rem<br>aperiam, eaque ipsa quae.</p>
  <div class="btn" style="top:457px">Read More</div>
</article>

<section class="abs how">
  <div class="photo video" role="img" aria-label="Video thumbnail about family law and divorce">
    <svg class="abs" style="left:218px;top:138px" width="78" height="78" viewBox="0 0 78 78"><circle cx="39" cy="39" r="34" fill="none" stroke="#fff" stroke-width="5"/><circle cx="39" cy="39" r="28" fill="#fff"/><path d="M31 25 L55 39 L31 53 Z" fill="#1c1c1c"/></svg>
  </div>
  <h2 class="section-title" style="left:615px;top:73px;color:var(--white)">How I Do It</h2>
  <div class="rule" style="left:615px;top:141px;width:178px;background:var(--white)"></div>
  <p class="body-text" style="left:615px;top:172px;color:var(--white)">Lorem ipsum dolor sit amet, consectetur adipiscing elit. Mauris sit amet<br>nunc lorem. Quisque id vestibulum mi. Fusce aliquet blandit laoreet.<br>Suspendisse condimentum ante eu quam ultrices, et malesuada mauris<br>malesuada. Praesent ac porta leo. Nunc iaculis tempus condimentum.<br>Integer accumsan nibh eget sodales rutrum.</p>
  <div class="btn" style="left:615px;top:348px;width:207px;height:54px;font-size:16px">Read More</div>
</section>

<h2 class="section-title" style="left:74px;top:2085px">Our Benefits</h2>
<div class="rule" style="left:74px;top:2151px;width:178px"></div>
<p class="body-text" style="left:74px;top:2185px;color:var(--text)">Sed ut perspiciatis unde omnis iste natus error sit voluptatem accusantium<br>doloremque laudantium, totam rem aperiam, eaque ipsa quae ab illo<br>inventore veritatis et quasi &nbsp;architecto beatae vitae dicta sunt explicabo.<br>Nemo enim ipsam voluptatem quia &nbsp;voluptas sit aspernatur aut odit aut<br>fugit, sed quia consequuntur magni dolores eos qui ratione<br>voluptatem sequi nesciunt.</p>
<div class="btn" style="left:74px;top:2394px;width:207px;height:54px;font-size:16px">Read More</div>
<div class="photo" role="img" aria-label="Family reviewing documents with a lawyer" style="left:615px;top:2093px;width:511px;height:355px;border-radius:22px;background:linear-gradient(135deg,#c9c2b8,#7c6e63 45%,#2b2a2d)"></div>

<section class="abs" style="left:0;top:2532px;width:1200px;height:789px;background:var(--blog-bg);border-top-left-radius:110px"></section>
<h2 class="section-title center" style="top:2607px">Recent Blog Articles</h2>
<div class="rule" style="left:509px;top:2672px;width:182px"></div>

<article class="card" style="left:74px;top:2728px;height:482px">
  <div class="card-photo" role="img" aria-label="Two men talking in an office" style="background:linear-gradient(135deg,#e3e3df,#8f8579 50%,#3c3f44)"></div>
  <h3 class="card-title" style="top:268px">Nemo Enim Ipsam<br>Voluptatem Quia Voluptas</h3>
  <p class="card-text" style="top:330px;line-height:26px">Sed ut perspiciatis unde omnis iste natus<br>error sit voluptatem accusantium<br>doloremque laudantium, totam rem<br>aperiam, eaque ipsa quae.</p>
  <div class="btn" style="top:458px">Read More</div>
</article>
<article class="card" style="left:435px;top:2728px;height:482px">
  <div class="card-photo" role="img" aria-label="Group reviewing papers at a wooden table" style="background:linear-gradient(135deg,#b99b76,#d8c6ae 50%,#5c5450)"></div>
  <h3 class="card-title" style="top:268px">Nemo Enim Ipsam<br>Voluptatem Quia Voluptas</h3>
  <p class="card-text" style="top:330px;line-height:26px">Sed ut perspiciatis unde omnis iste natus<br>error sit voluptatem accusantium<br>doloremque laudantium, totam rem<br>aperiam, eaque ipsa quae.</p>
  <div class="btn" style="top:458px">Read More</div>
</article>
<article class="card" style="left:800px;top:2728px;height:482px">
  <div class="card-photo" role="img" aria-label="Family meeting with an advisor at a desk" style="background:linear-gradient(135deg,#8d7c6e,#c8b8a5 45%,#3a3a40)"></div>
  <h3 class="card-title" style="top:268px">Nemo Enim Ipsam<br>Voluptatem Quia Voluptas</h3>
  <p class="card-text" style="top:330px;line-height:26px">Sed ut perspiciatis unde omnis iste natus<br>error sit voluptatem accusantium<br>doloremque laudantium, totam rem<br>aperiam, eaque ipsa quae.</p>
  <div class="btn" style="top:458px">Read More</div>
</article>

<h2 class="section-title center" style="top:3381px">Contact Vellmore Family Law</h2>
<div class="rule" style="left:509px;top:3446px;width:182px"></div>

<form>
  <div class="field" style="left:74px;top:3502px;width:332px">Fullname</div>
  <div class="field" style="left:435px;top:3502px;width:332px">Email Address</div>
  <div class="field" style="left:793px;top:3502px;width:333px">Phone No</div>
  <div class="field" style="left:74px;top:3568px;width:332px">Select Services<svg width="8" height="12" viewBox="0 0 8 12"><path d="M4 0L8 5H0zM4 12L0 7h8z" fill="#333"/></svg></div>
  <div class="field" style="left:435px;top:3568px;width:332px">Select Location*<svg width="8" height="12" viewBox="0 0 8 12"><path d="M4 0L8 5H0zM4 12L0 7h8z" fill="#333"/></svg></div>
  <div class="field" style="left:793px;top:3568px;width:333px">Zip Code</div>
  <div class="field area" style="left:74px;top:3637px;width:1052px">Message</div>
  <div class="btn" style="left:496px;top:3861px;width:208px;height:54px;font-size:16px">Submit</div>
</form>

<section class="photo cta" role="img" aria-label="City skyline at night with a golden tint">
  <h2 class="hero-title big" style="top:82px">Vellmore Family Law</h2>
  <p class="hero-title sub" style="top:160px">Collaborative Law and Unbundled Legal Service</p>
  <p class="hero-title sub" style="top:210px">in King County, Washington State</p>
  <div class="btn" style="left:496px;top:287px;width:208px;height:54px;font-size:16px">Contact Us</div>
</section>

<footer class="abs site-footer">
  <div class="brand" style="left:74px;top:122px">
    <div class="brand-mark"></div>
    <div class="brand-name">Vellmore<br>Family Law</div>
  </div>
  <div class="foot-col" style="left:396px;top:50px">
    <h4>Site Map</h4>
    <p>Home</p><p>About</p><p>Practice Areas</p><p>Latest News</p><p>Contact Us</p>
  </div>
  <div class="foot-col" style="left:641px;top:50px">
    <h4>Resources</h4>
    <p>Sed ut perspiciatis</p><p>Unde omnis iste</p><p>Natus error sit voluptatem</p><p>Accusantium</p>
  </div>
  <div class="foot-col" style="left:911px;top:50px">
    <h4>Contact Info</h4>
    <p style="line-height:25px">Sed ut perspiciatis<br>Unde omnis iste natus error</p>
    <p style="display:flex;align-items:center;gap:14px;margin-top:4px"><svg width="14" height="14" viewBox="0 0 24 24" fill="#fff"><path d="M6.6 10.8a15.1 15.1 0 0 0 6.6 6.6l2.2-2.2a1 1 0 0 1 1-.25 11.4 11.4 0 0 0 3.6.57 1 1 0 0 1 1 1V20a1 1 0 0 1-1 1A17 17 0 0 1 3 4a1 1 0 0 1 1-1h3.5a1 1 0 0 1 1 1c0 1.25.2 2.45.57 3.6a1 1 0 0 1-.25 1z"/></svg>1-800-555-0148</p>
    <p style="display:flex;align-items:center;gap:14px;line-height:26px"><svg width="14" height="12" viewBox="0 0 14 12"><rect width="14" height="12" rx="1" fill="#fff"/><path d="M0 1l7 5 7-5" stroke="#1b1b1b" stroke-width="1.4" fill="none"/></svg>info@vellmorelaw.com</p>
  </div>
  <div class="btn gold" style="left:950px;top:254px;width:176px;height:48px;border-radius:10px 10px 0 0;gap:8px;font-size:15px">
    <svg width="18" height="15" viewBox="0 0 18 15" fill="#fff"><path d="M2 1h11a2 2 0 0 1 2 2v5a2 2 0 0 1-2 2H7l-4 3v-3H2a2 2 0 0 1-2-2V3a2 2 0 0 1 2-2z"/></svg>Live Chat
  </div>
  <div class="foot-bar">
    <p class="abs" style="left:74px;top:21px">Copyright ©2021 Vellmore Family Law. All Rights Reserved.</p>
    <div class="social" style="left:950px"><i></i><i></i><i></i><i></i><i></i></div>
  </div>
</footer>

</body>
</html>
```